wealth management firm, professional group, new model

we have a logo that works but we need a card, white background using our colors...clean look

our tag line if can be used in

Guiding Every Client Toward Ownership

```html
<!DOCTYPE html>
<html lang="en">
<head>
<meta charset="utf-8">
<title>Northvale – Business Card</title>
<link rel="stylesheet" href="https://fonts.googleapis.com/css2?family=Montserrat:wght@400;500;700&display=swap">
<style>
  :root {
    --navy: #142459;
    --paper: #f4f5f7;
    --backdrop: #8a8a8a;
    --white: #ffffff;
  }
  * { box-sizing: border-box; margin: 0; padding: 0; }
  html, body { width: 1200px; height: 1050px; overflow: hidden; }
  body {
    background: var(--backdrop);
    font-family: "Montserrat", sans-serif;
    position: relative;
  }
  .card {
    position: absolute;
    width: 560px;
    height: 320px;
    border-radius: 4px;
    box-shadow: 0 18px 40px rgba(0,0,0,0.25);
  }
  .wordmark {
    display: flex;
    align-items: center;
    gap: 12px;
    white-space: nowrap;
  }
  .wordmark-mark { flex: none; background: currentColor; }
  .wordmark-name { font-weight: 500; letter-spacing: 0.01em; line-height: 1; }

  /* Brand side */
  .card-back {
    left: 560px; top: 150px;
    background: var(--navy);
    color: var(--white);
  }
  .card-back .wordmark {
    position: absolute;
    left: 0; right: 0; top: 108px;
    justify-content: center;
  }
  .card-back .wordmark-mark { width: 16px; height: 16px; }
  .card-back .wordmark-name { font-size: 40px; }
  .tagline-rule {
    position: absolute;
    left: 24px; right: 24px; top: 226px;
    display: flex; align-items: center; gap: 12px;
  }
  .tagline-rule::before, .tagline-rule::after {
    content: ""; flex: 1; height: 1px; background: var(--white);
  }
  .tagline { font-size: 14px; font-weight: 500; letter-spacing: 0.04em; white-space: nowrap; }

  /* Contact side */
  .card-front {
    left: 80px; top: 580px;
    background: var(--paper);
    color: var(--navy);
  }
  .contact { position: absolute; left: 34px; top: 58px; width: 270px; }
  .contact-name { font-size: 22px; font-weight: 700; letter-spacing: 0.01em; text-transform: uppercase; }
  .contact-role { font-size: 14px; font-weight: 500; margin-bottom: 12px; }
  .contact-address { font-size: 13px; font-weight: 500; line-height: 1.45; margin-bottom: 10px; }
  .contact-list { list-style: none; font-size: 13px; font-weight: 500; line-height: 1.7; }
  .contact-list li { display: flex; align-items: center; gap: 7px; }
  .contact-list svg { width: 12px; height: 12px; fill: var(--navy); flex: none; }
  .card-front .wordmark { position: absolute; right: 40px; top: 136px; }
  .card-front .wordmark-mark { width: 11px; height: 11px; }
  .card-front .wordmark-name { font-size: 28px; }
</style>
</head>
<body>
  <section class="card card-back" aria-label="Card back">
    <div class="wordmark">
      <span class="wordmark-mark" aria-hidden="true"></span>
      <p class="wordmark-name">Northvale</p>
    </div>
    <div class="tagline-rule">
      <p class="tagline">Guiding Every Client Toward Ownership</p>
    </div>
  </section>

  <section class="card card-front" aria-label="Card front">
    <div class="contact">
      <h1 class="contact-name">Daniel Hartley</h1>
      <p class="contact-role">Advisor</p>
      <p class="contact-address">480 Linden Row Ave<br>Maple Grove, FL 32700</p>
      <ul class="contact-list">
        <li><svg viewBox="0 0 24 24" aria-hidden="true"><path d="M6.6 10.8a15.1 15.1 0 0 0 6.6 6.6l2.2-2.2a1 1 0 0 1 1-.25 11.4 11.4 0 0 0 3.6.57 1 1 0 0 1 1 1V20a1 1 0 0 1-1 1A17 17 0 0 1 3 4a1 1 0 0 1 1-1h3.5a1 1 0 0 1 1 1c0 1.25.2 2.45.57 3.57a1 1 0 0 1-.25 1z"/></svg>555-014-2290</li>
        <li><svg viewBox="0 0 24 24" aria-hidden="true"><path d="M2 5h20v14H2zm2 2v.2l8 5.8 8-5.8V7z"/></svg>hello@northvale.com</li>
        <li><svg viewBox="0 0 24 24" aria-hidden="true"><path d="M12 2a10 10 0 1 0 0 20 10 10 0 0 0 0-20zm6.9 6h-3a15.6 15.6 0 0 0-1.4-3.6A8 8 0 0 1 18.9 8zM12 4a14 14 0 0 1 1.9 4h-3.8A14 14 0 0 1 12 4zM4.3 14a8 8 0 0 1 0-4h3.4a16.5 16.5 0 0 0 0 4zm.8 2h3a15.6 15.6 0 0 0 1.4 3.6A8 8 0 0 1 5.1 16zm3-8h-3a8 8 0 0 1 4.4-3.6A15.6 15.6 0 0 0 8.1 8zM12 20a14 14 0 0 1-1.9-4h3.8A14 14 0 0 1 12 20zm2.3-6H9.7a14.7 14.7 0 0 1 0-4h4.6a14.7 14.7 0 0 1 0 4zm.2 5.6a15.6 15.6 0 0 0 1.4-3.6h3a8 8 0 0 1-4.4 3.6zm1.8-5.6a16.5 16.5 0 0 0 0-4h3.4a8 8 0 0 1 0 4z"/></svg>northvale.com</li>
      </ul>
    </div>
    <div class="wordmark">
      <span class="wordmark-mark" aria-hidden="true"></span>
      <p class="wordmark-name">Northvale</p>
    </div>
  </section>
</body>
</html>
```